Corvin Ridge Software PowerPoint template

We are a software company selling endpoint visibility, access and security technology to enterprise-level IT departments.
Our technology helps organizations gain comprehensive visibility into and control over devices accessing their corporate network so they can quickly identify and address suspicious activity on the network that could lead to potential threats like data breaches.
This technology can cost organizations upwards of $1M - depending on the size of the organization. Our primary clients are Vestral 2,000 companies.
We want a professional, polished PowerPoint template that we can use for all company presentations. Please include:
Title page
Section page
General info page
Thank you page
Logo options and color specs are attached.
Please include our tagline on at least the title page: Discover the edge. Optimize the whole.
Reason: Seeking more options. Looking for a clean design that uses lots of white space.
Software

```html
<!DOCTYPE html>
<html lang="en">
<head>
<meta charset="utf-8">
<title>Corvin Ridge Software — Title Slide</title>
<link rel="stylesheet" href="https://fonts.googleapis.com/css2?family=Ubuntu:wght@300;400;500;700&family=Open+Sans:wght@600;700&display=swap">
<style>
  :root {
    --brand-red: #8c1b22;
    --brand-copper: #d1825b;
    --text-grey: #767676;
    --muted-grey: #555555;
    --paper: #ffffff;
  }
  * { margin: 0; padding: 0; box-sizing: border-box; }
  html, body {
    width: 1200px;
    height: 849px;
    overflow: hidden;
    background: var(--paper);
  }
  .slide {
    position: relative;
    width: 1200px;
    height: 849px;
    background: var(--paper);
    font-family: "Ubuntu", "Helvetica Neue", Arial, sans-serif;
  }

  /* Brand lockup, top right */
  .brand {
    position: absolute;
    left: 712px;
    top: 82px;
    display: flex;
    align-items: center;
    gap: 26px;
    color: var(--brand-red);
  }
  .brand-mark {
    width: 72px;
    height: 72px;
    flex: none;
  }
  .brand-name {
    font-weight: 500;
    line-height: 1;
  }
  .brand-name .line-main {
    display: block;
    font-size: 34px;
    letter-spacing: 2px;
  }
  .brand-name .line-sub {
    display: block;
    margin-top: 10px;
    font-size: 20px;
    letter-spacing: 14px;
  }

  /* Title block */
  .tagline {
    position: absolute;
    left: 128px;
    top: 344px;
    font-weight: 300;
    font-size: 65px;
    line-height: 71px;
    color: var(--brand-red);
    text-transform: uppercase;
    letter-spacing: 0.5px;
  }
  .presentee {
    position: absolute;
    left: 129px;
    top: 527px;
    font-weight: 500;
    font-size: 22px;
    color: var(--text-grey);
    text-transform: uppercase;
  }
  .date {
    position: absolute;
    left: 129px;
    top: 564px;
    font-weight: 300;
    font-size: 21px;
    color: var(--text-grey);
    text-transform: uppercase;
  }

  /* Footer */
  .web-address {
    position: absolute;
    left: 130px;
    top: 756px;
    font-size: 17px;
    font-weight: 400;
    color: var(--brand-red);
    text-transform: uppercase;
  }
  .web-address strong { font-weight: 700; }
  .footer-band {
    position: absolute;
    left: 443px;
    top: 760px;
    width: 743px;
    height: 11px;
    background: var(--brand-copper);
  }
  .copyright {
    position: absolute;
    right: 90px;
    top: 779px;
    font-family: "Open Sans", Arial, sans-serif;
    font-weight: 700;
    font-size: 11px;
    color: var(--muted-grey);
  }
</style>
</head>
<body>
  <main class="slide">
    <header class="brand">
      <svg class="brand-mark" viewBox="0 0 72 72" aria-hidden="true">
        <circle cx="36" cy="36" r="30" fill="var(--brand-copper)"/>
      </svg>
      <div class="brand-name">
        <span class="line-main">CORVIN RIDGE</span>
        <span class="line-sub">SOFTWARE</span>
      </div>
    </header>

    <h1 class="tagline">Discover the edge,<br>Optimize the whole</h1>
    <p class="presentee">Name of the presentee</p>
    <p class="date">Date : MM DD YY</p>

    <footer>
      <p class="web-address">www. <strong>corvinridge</strong>software.com</p>
      <div class="footer-band"></div>
      <p class="copyright">©2015 Corvin Ridge Software</p>
    </footer>
  </main>
</body>
</html>
```